indépendant en tant que Massothérapeute et Préparateur Mental, j'ai besoin de ...

Massothérapeute et préparateur mental indépendant, je recherche une carte de visite sobre et dynamique, sans images liées au massage ou à la préparation mentale mais intégrant mon logo. Les couleurs que j'aime bien sont : Blanc, gris, anthracite, noir et jaune

Contact Information for Business Card

carte de préférence Horizontale
neutre qui puisse toucher le deux domaines Massothérapie et préparation mentale

Requirements
Must have
• mon projet doit intégrer au recto:
LOGO
Loïc Bardèze
078 513 26 48
info@loicbardeze.ch
et éventuellement www.loicbardeze.ch

et au verso les deux adresses:

Chemin des Ormilles 7B
1400 Yverdon-les-Bains

Route de la Gravière 9
1630 Bulle

Should not have
• mon projet ne doit pas contenir d'image en liens avec le massage ni la préparation mentale.

```html
<!DOCTYPE html>
<html lang="fr">
<head>
<meta charset="utf-8">
<title>Loïc Bardèze – Carte de visite</title>
<link rel="stylesheet" href="https://fonts.googleapis.com/css2?family=Roboto:wght@400;700&display=swap">
<style>
  :root {
    --backdrop: #d9d9db;
    --card: #121012;
    --ink-light: #f2f2f2;
    --ink-muted: #b9b9bb;
    --ink-dark: #2a282a;
    --silver: #a8a2a6;
  }
  html, body {
    margin: 0;
    width: 1200px;
    height: 800px;
    overflow: hidden;
    background: var(--backdrop);
    font-family: "Roboto", sans-serif;
  }
  .canvas {
    position: relative;
    width: 1200px;
    height: 800px;
    display: flex;
    align-items: center;
    justify-content: center;
    gap: 56px;
  }
  .card {
    position: relative;
    width: 520px;
    height: 336px;
    background: var(--card);
    border-radius: 26px;
    box-sizing: border-box;
  }
  /* Recto: brand left, contact right */
  .card--front .brand {
    position: absolute;
    left: 40px;
    top: 150px;
  }
  .brand-line {
    display: flex;
    align-items: center;
    gap: 12px;
  }
  .brand-mark {
    width: 18px;
    height: 18px;
    border-radius: 50%;
    background: var(--ink-light);
  }
  .brand-name {
    font-size: 24px;
    font-weight: 400;
    color: var(--ink-light);
    letter-spacing: 0.5px;
  }
  .brand-tagline {
    margin: 6px 0 0 30px;
    font-size: 9px;
    letter-spacing: 0.4px;
    text-transform: uppercase;
    color: var(--ink-muted);
    white-space: nowrap;
  }
  .divider {
    position: absolute;
    left: 292px;
    top: 52px;
    width: 1px;
    height: 232px;
    background: var(--ink-light);
  }
  .contact {
    position: absolute;
    left: 312px;
    top: 50px;
    color: var(--ink-light);
    font-size: 13px;
    line-height: 17px;
  }
  .contact-name {
    font-size: 17px;
    font-weight: 700;
    margin: 0 0 12px;
  }
  .contact-address {
    margin: 0 0 8px;
    font-style: normal;
  }
  .contact-list {
    list-style: none;
    margin: 0;
    padding: 0;
  }
  .contact-list li {
    display: flex;
    align-items: center;
    gap: 7px;
  }
  .contact-list svg {
    width: 10px;
    height: 10px;
    flex: none;
  }
  /* Verso: centred brand, tone-on-tone */
  .card--back .brand {
    position: absolute;
    left: 50%;
    top: 50%;
    transform: translate(-50%, -50%);
  }
  .card--back .brand-mark {
    width: 34px;
    height: 34px;
    background: linear-gradient(135deg, #d8d2d6, var(--silver) 55%, #6e686c);
  }
  .card--back .brand-name {
    font-size: 30px;
    color: var(--ink-dark);
  }
  .card--back .brand-tagline {
    margin-left: 46px;
    color: var(--ink-dark);
  }
</style>
</head>
<body>
<main class="canvas">
  <section class="card card--front" aria-label="Recto">
    <div class="brand">
      <div class="brand-line">
        <span class="brand-mark"></span>
        <span class="brand-name">Loïc Bardèze</span>
      </div>
      <p class="brand-tagline">Massothérapeute / Préparateur Mental</p>
    </div>
    <div class="divider"></div>
    <div class="contact">
      <p class="contact-name">Loïc Bardèze</p>
      <address class="contact-address">Chemin des Ormilles 7B<br>1350 Orbe</address>
      <address class="contact-address">Route de la Gravière 9<br>1630 Bulle</address>
      <ul class="contact-list">
        <li>
          <svg viewBox="0 0 10 10" aria-hidden="true"><path d="M2 1 L4 1 L4.6 3 L3.5 3.8 Q4.5 5.8 6.2 6.5 L7 5.4 L9 6 L9 8 Q5 9 1.8 5.2 Q0.8 3 2 1 Z" fill="#f2f2f2"/></svg>
          078 513 26 48
        </li>
        <li>
          <svg viewBox="0 0 10 10" aria-hidden="true"><rect x="0.5" y="2" width="9" height="6.5" fill="#f2f2f2"/><path d="M0.5 2 L5 5.8 L9.5 2" fill="none" stroke="#121012" stroke-width="0.9"/></svg>
          info@loicbardeze.ch
        </li>
        <li>
          <svg viewBox="0 0 10 10" aria-hidden="true"><circle cx="5" cy="5" r="4.5" fill="#f2f2f2"/><path d="M0.5 5 H9.5 M5 0.5 Q2.5 5 5 9.5 M5 0.5 Q7.5 5 5 9.5" fill="none" stroke="#121012" stroke-width="0.7"/></svg>
          www.loicbardeze.ch
        </li>
      </ul>
    </div>
  </section>

  <section class="card card--back" aria-label="Verso">
    <div class="brand">
      <div class="brand-line">
        <span class="brand-mark"></span>
        <span class="brand-name">Loïc Bardèze</span>
      </div>
      <p class="brand-tagline">Massothérapeute / Préparateur Mental</p>
    </div>
  </section>
</main>
</body>
</html>
```